Brightmere Facebook Design

Build out a really nice and professional Facebook Page and full banner for Brightmere perhaps with the our services portfolio across the page as well,
Pls check www.brightmere-example.com.au for ideas to a make the Facebook Page look professional like a similar theme to our website and the porfolio of services

Main photo please emphasis the equipment cleaning and the gurney cleaning a lower priority to emphasize is the general cleaning
Thanks very much

Target Market(s)

Restaurant, warehouses, factories, car and fleet companies, hotels and buffets, chain restaurants, pizza huts, burger eateries, leisure centres

Industry/Entity Type

Cleaning Services

Font styles to use
Serif

Colors
3277b5
f04a50
f37122
fcf299
ec1f27

Requirements
Must have
• Energy and professional Facebook Site with some of the Brightmere Flowers across it and the portfolio of services
Nice to have
• Good vibrant colours

Professional similar to the website

```html
<!DOCTYPE html>
<html lang="en">
<head>
<meta charset="utf-8">
<title>Brightmere – Social Page</title>
<link rel="stylesheet" href="https://fonts.googleapis.com/css2?family=Crimson+Pro:wght@400;500&family=Source+Sans+3:wght@400;600;700&display=swap">
<style>
  :root {
    --topbar: #5260a8;
    --page-bg: #e9ebf0;
    --card: #ffffff;
    --navy: #123d6b;
    --orange: #ef6f26;
    --link-blue: #4a55a2;
    --ink: #1d1d1f;
    --muted: #8a8f9c;
    --bar-grey: #dcdde1;
    --line: #e2e4e9;
    --tile: #f8f19b;
    --btn-border: #5a64a8;
  }
  * { box-sizing: border-box; margin: 0; padding: 0; }
  html, body { width: 1015px; height: 1200px; overflow: hidden; }
  body {
    background: var(--page-bg);
    font-family: "Source Sans 3", Arial, sans-serif;
    color: var(--ink);
    position: relative;
  }
  .abs { position: absolute; }

  /* Top navigation */
  .topbar { left: 0; top: 0; width: 1015px; height: 49px; background: var(--topbar); }
  .topbar .home-square { left: 87px; top: 11px; width: 28px; height: 28px; background: #fff; border-radius: 3px; }
  .topbar .search { left: 171px; top: 12px; width: 297px; height: 26px; background: #fff; border-radius: 3px; }
  .topbar .search svg { position: absolute; right: 8px; top: 6px; }
  .topbar .avatar { left: 509px; top: 13px; width: 26px; height: 26px; border-radius: 50%; background: #f2a23a; border: 2px solid #fff; }
  .topbar .user { left: 545px; top: 16px; color: #fff; font-size: 14px; font-weight: 600; }
  .topbar .home { left: 627px; top: 16px; color: #fff; font-size: 14px; font-weight: 600; }
  .topbar .icon { top: 15px; }

  /* Left column */
  .profile-pic { left: 22px; top: 67px; width: 154px; height: 154px; border-radius: 50%; background: #fff;
    display: flex; align-items: center; justify-content: center; }
  .profile-pic span { font-family: "Crimson Pro", Georgia, serif; font-size: 28px; color: var(--navy); font-weight: 500; }
  .page-name { left: 35px; top: 268px; font-size: 21px; font-weight: 400; }
  .page-handle { left: 35px; top: 298px; font-size: 12.5px; }
  .side-bar { left: 35px; width: 108px; height: 10px; background: var(--bar-grey); }

  /* Cover */
  .cover { left: 193px; top: 67px; width: 786px; height: 289px;
    background: linear-gradient(120deg, #6b6561 0%, #b9b6b3 30%, #8f8a86 55%, #c9c4bf 75%, #4d4845 100%); }
  .cover-panel { left: 48px; top: 35px; width: 690px; height: 219px; background: rgba(255,255,255,0.66);
    display: flex; flex-direction: column; align-items: center; justify-content: center; }
  .cover-mark { display: flex; align-items: center; gap: 14px; margin-top: -18px; }
  .cover-mark .dot { width: 34px; height: 34px; border-radius: 50%; background: var(--navy); }
  .cover-mark .name { font-family: "Crimson Pro", Georgia, serif; font-size: 50px; color: var(--navy); line-height: 1; }
  .cover-tagline { font-family: "Crimson Pro", Georgia, serif; font-size: 22px; color: var(--navy); margin-top: 4px; margin-left: 86px; }

  .action-bar { left: 193px; top: 356px; width: 786px; height: 42px; background: var(--card); }
  .btn { position: absolute; top: 12px; height: 24px; border: 1px solid var(--btn-border); border-radius: 3px;
    font-size: 10px; font-weight: 600; display: flex; align-items: center; background: #fff; }
  .btn-like { left: 18px; width: 56px; gap: 4px; padding-left: 6px; }
  .btn-group { left: 85px; width: 181px; }
  .btn-group .seg { height: 100%; display: flex; align-items: center; gap: 4px; padding: 0 7px; border-right: 1px solid var(--btn-border); }
  .btn-group .seg:last-child { border-right: none; flex: 1; justify-content: center; }
  .btn-group .follow { color: var(--muted); font-weight: 400; }

  /* Post */
  .post { left: 193px; top: 412px; width: 467px; height: 385px; background: var(--card); }
  .post-avatar { left: 24px; top: 12px; width: 52px; height: 52px; border-radius: 50%; background: #fff; border: 1px solid var(--line);
    display: flex; align-items: center; justify-content: center; font-family: "Crimson Pro", Georgia, serif; font-size: 10px; color: var(--navy); }
  .post-author { left: 93px; top: 17px; font-size: 14.5px; color: var(--link-blue); }
  .post-time { left: 93px; top: 37px; font-size: 9.5px; color: var(--muted); }
  .post-link { left: 23px; top: 71px; width: 411px; height: 265px; border: 1px solid var(--line); border-top: none; }
  .post-photo { left: 43px; top: 71px; width: 368px; height: 171px;
    background: linear-gradient(100deg, #d9dbdc 0%, #8fb3c9 35%, #f0f0ee 60%, #c5c8ca 100%); }
  .post-title { left: 35px; top: 255px; font-size: 15.5px; color: var(--link-blue); }
  .post-line { left: 35px; height: 4px; background: var(--bar-grey); }
  .post-cta { left: 362px; top: 265px; width: 55px; height: 24px; border: 1px solid #c9ccd3; }
  .post-divider { left: 0; top: 337px; width: 467px; height: 1px; background: var(--line); }
  .post-actions { left: 33px; top: 353px; display: flex; gap: 18px; font-size: 12.5px; color: var(--muted); }
  .post-actions span { display: flex; align-items: center; gap: 5px; }

  /* About */
  .about { left: 673px; top: 413px; width: 306px; height: 356px; background: var(--card); }
  .about-head { left: 0; top: 0; width: 306px; height: 140px; background: var(--orange); }
  .about-mark { left: 0; top: 45px; width: 306px; display: flex; justify-content: center; align-items: center; gap: 9px; }
  .about-mark .dot { width: 22px; height: 22px; border-radius: 50%; background: #fff; }
  .about-mark .name { font-family: "Crimson Pro", Georgia, serif; font-size: 32px; color: #fff; line-height: 1; }
  .about-label { left: 40px; top: 113px; font-size: 12px; color: #fff; font-weight: 600; }
  .about-heading { left: 32px; top: 158px; font-size: 11px; font-weight: 700; color: #3b3d45; letter-spacing: 0.1px; }
  .about-text { left: 34px; top: 188px; width: 229px; font-size: 11.6px; line-height: 14.4px; text-align: justify; color: #111; }
  .about-text p + p { margin-top: 14px; }

  /* Services gallery */
  .gallery { left: 673px; top: 787px; width: 306px; height: 318px; background: var(--card); }
  .tile { position: absolute; width: 87px; height: 86px; background: var(--tile); }
</style>
</head>
<body>

<header class="abs topbar">
  <div class="abs home-square"></div>
  <div class="abs search">
    <svg width="14" height="14" viewBox="0 0 14 14"><circle cx="5.5" cy="5.5" r="4" fill="none" stroke="#2b3360" stroke-width="2"/><line x1="8.5" y1="8.5" x2="13" y2="13" stroke="#2b3360" stroke-width="2.4"/></svg>
  </div>
  <div class="abs avatar"></div>
  <div class="abs user">tova</div>
  <div class="abs home">Home</div>
  <svg class="abs icon" style="left:702px" width="22" height="18" viewBox="0 0 22 18" fill="#2f3670"><circle cx="7" cy="5" r="4"/><circle cx="15" cy="5" r="3.5"/><path d="M0 17c0-5 3-7 7-7s7 2 7 7z"/><path d="M13 10c4 0 8 2 8 7h-6c0-3-1-5-2-7z"/></svg>
  <svg class="abs icon" style="left:741px" width="18" height="18" viewBox="0 0 18 18" fill="#2f3670"><path d="M9 1C4.6 1 1 4.3 1 8.3c0 2.3 1.1 4.3 2.9 5.6V17l2.8-1.5c.7.2 1.5.3 2.3.3 4.4 0 8-3.3 8-7.5S13.4 1 9 1z"/></svg>
  <svg class="abs icon" style="left:776px" width="18" height="18" viewBox="0 0 18 18"><circle cx="9" cy="9" r="8" fill="#2f3670"/><circle cx="9" cy="9" r="3" fill="var(--topbar)"/></svg>
  <svg class="abs icon" style="left:813px" width="20" height="18" viewBox="0 0 20 18" fill="#2f3670"><rect x="1" y="6" width="15" height="11" rx="1"/><rect x="6" y="1" width="6" height="6" rx="1"/><circle cx="17" cy="4" r="3"/></svg>
  <svg class="abs icon" style="left:850px;top:21px" width="10" height="6" viewBox="0 0 10 6" fill="#2f3670"><path d="M0 0h10L5 6z"/></svg>
</header>

<aside>
  <div class="abs profile-pic"><span>Brightmere</span></div>
  <div class="abs page-name">Brightmere</div>
  <div class="abs page-handle">@Brightmere</div>
  <div class="abs side-bar" style="top:353px"></div>
  <div class="abs side-bar" style="top:379px"></div>
  <div class="abs side-bar" style="top:404px"></div>
  <div class="abs side-bar" style="top:430px"></div>
</aside>

<section class="abs cover" role="img" aria-label="Photo of a commercial stainless steel kitchen with hanging lamps">
  <div class="abs cover-panel">
    <div class="cover-mark"><div class="dot"></div><div class="name">Brightmere</div></div>
    <div class="cover-tagline">Service · Management · Cleaning</div>
  </div>
</section>

<nav class="abs action-bar">
  <div class="btn btn-like">
    <svg width="14" height="13" viewBox="0 0 14 13" fill="var(--link-blue)"><rect x="0" y="5" width="3" height="8"/><path d="M4 5l3-5c1.5 0 2 1 1.6 2.5L8 5h5c.8 0 1.2.7 1 1.4l-1.5 5.6c-.2.6-.6 1-1.2 1H4z"/></svg>
    Like
  </div>
  <div class="btn btn-group">
    <div class="seg follow">+ Follow</div>
    <div class="seg">
      <svg width="15" height="12" viewBox="0 0 15 12" fill="#4a4f63"><path d="M0 0h15v9H5l-3 3V9H0z"/></svg>
      Message
    </div>
    <div class="seg">
      <svg width="20" height="5" viewBox="0 0 20 5" fill="#3a3f55"><circle cx="2.5" cy="2.5" r="2.3"/><circle cx="10" cy="2.5" r="2.3"/><circle cx="17.5" cy="2.5" r="2.3"/></svg>
    </div>
  </div>
</nav>

<article class="abs post">
  <div class="abs post-avatar">Brightmere</div>
  <div class="abs post-author">Brightmere</div>
  <div class="abs post-time">6 minutes ago</div>
  <div class="abs post-link"></div>
  <div class="abs post-photo" role="img" aria-label="Photo of cleaners in blue aprons vacuuming a bright office floor"></div>
  <div class="abs post-title">Keeping your office fresh and clean</div>
  <div class="abs post-line" style="top:280px;width:165px"></div>
  <div class="abs post-line" style="top:294px;width:165px"></div>
  <div class="abs post-line" style="top:309px;width:120px"></div>
  <div class="abs post-cta"></div>
  <div class="abs post-divider"></div>
  <div class="abs post-actions">
    <span><svg width="14" height="13" viewBox="0 0 14 13" fill="var(--muted)"><rect x="0" y="5" width="3" height="8"/><path d="M4 5l3-5c1.5 0 2 1 1.6 2.5L8 5h5c.8 0 1.2.7 1 1.4l-1.5 5.6c-.2.6-.6 1-1.2 1H4z"/></svg>Like</span>
    <span><svg width="14" height="14" viewBox="0 0 14 14" fill="var(--muted)"><path d="M7 1C3.7 1 1 3.4 1 6.4c0 1.7.9 3.2 2.2 4.2V13l2.2-1.2c.5.1 1 .2 1.6.2 3.3 0 6-2.4 6-5.6S10.3 1 7 1z"/></svg>Comment</span>
    <span><svg width="17" height="13" viewBox="0 0 17 13" fill="var(--muted)"><path d="M10 0l7 6-7 6V8.5C5 8.5 2 10 0 13c.7-5 3.5-8.5 10-9.3z"/></svg>Share</span>
  </div>
</article>

<section class="abs about">
  <div class="abs about-head">
    <div class="abs about-mark"><div class="dot"></div><div class="name">Brightmere</div></div>
    <div class="abs about-label">About Page</div>
  </div>
  <h2 class="abs about-heading">WE HAVE BEEN IN BUSINESS FOR 15 YEARS.</h2>
  <div class="abs about-text">
    <p>We have been in the Commercial Cleaning and Maintenance business for 15 years. We have built a strong and steady reputation. Our people are professional, reliable and customer service focused.</p>
    <p>Our purpose is to provide high quality hygiene and sanitisation services to each of our dedicated portfolios across equipment</p>
  </div>
</section>

<section class="abs gallery" aria-label="Services portfolio">
  <div class="tile" style="left:16px;top:20px"></div>
  <div class="tile" style="left:109px;top:20px"></div>
  <div class="tile" style="left:201px;top:20px"></div>
  <div class="tile" style="left:16px;top:112px"></div>
  <div class="tile" style="left:109px;top:112px"></div>
  <div class="tile" style="left:201px;top:112px"></div>
  <div class="tile" style="left:16px;top:205px"></div>
  <div class="tile" style="left:109px;top:205px"></div>
</section>

</body>
</html>
```